Every Shelf Set Neatly or ESN Organized needs a business card design. ESN Organized is a professi

We need a business card design that is clean, sharp and conveys a sense of organization. I already have a logo.

Target Market(s)

Families (specifically mothers), small business owners, parents, seniors

Industry/Entity Type

Business

Contact Information for Business Card

My website is www.esnorganized-example.com and my Facebook page is http://www.sociallink-example.com/everyshelfsetneatly. The phone number is 418-552-7094 and I want to be listed as Lorna M. Pelham, Owner

Requirements
Must have
• My logo.

```html
<!DOCTYPE html>
<html lang="en">
<head>
<meta charset="utf-8">
<title>ESN Organized – Business Card</title>
<link rel="stylesheet" href="https://fonts.googleapis.com/css2?family=Montserrat:wght@300;400&family=Open+Sans:wght@400;700&display=swap">
<style>
  :root {
    --page-bg: #e9e9e7;
    --card-black: #0b0b0c;
    --card-black-soft: #1c1c1e;
    --brand-blue: #0a7fe0;
    --text-white: #ffffff;
    --text-muted: #e4e4e4;
  }
  * { box-sizing: border-box; margin: 0; padding: 0; }
  html, body {
    width: 1200px; height: 900px; overflow: hidden;
    background: var(--page-bg);
  }
  .canvas {
    position: relative; width: 1200px; height: 900px;
    display: flex; flex-direction: column; align-items: center; justify-content: center; gap: 40px;
  }
  .card {
    position: relative; width: 560px; height: 320px; overflow: hidden;
    background: radial-gradient(ellipse at 50% 40%, var(--card-black-soft), var(--card-black) 75%);
    box-shadow: 0 6px 18px rgba(0,0,0,.25);
  }

  /* Front side */
  .card-front {
    display: flex; flex-direction: column; align-items: center; justify-content: center;
    color: var(--text-white); font-family: "Montserrat", sans-serif; font-weight: 300;
  }
  .front-logo { font-size: 62px; letter-spacing: 4px; line-height: 1; margin-bottom: 14px; }
  .front-tagline-top { font-size: 27px; letter-spacing: 5px; line-height: 1.1; }
  .front-tagline-main { font-size: 44px; letter-spacing: 14px; line-height: 1.15; margin-left: 14px; }
  .front-social {
    display: flex; align-items: center; gap: 8px; margin-top: 30px;
    font-size: 15px; font-weight: 400;
  }
  .social-square { width: 17px; height: 17px; background: var(--text-white); border-radius: 2px; }

  /* Back side */
  .card-back { font-family: "Open Sans", sans-serif; }
  .back-wave { position: absolute; inset: 0; width: 100%; height: 100%; }
  .back-logo {
    position: absolute; top: 28px; right: 52px;
    font-family: "Montserrat", sans-serif; font-weight: 300;
    font-size: 78px; letter-spacing: 3px; line-height: 1; color: var(--brand-blue);
  }
  .owner-name {
    position: absolute; top: 62px; left: 40px;
    font-weight: 700; font-size: 18px; color: var(--brand-blue);
  }
  .owner-role {
    position: absolute; top: 88px; left: 48px;
    font-size: 14px; color: var(--text-muted);
  }
  .contact-list {
    position: absolute; top: 140px; left: 70px; list-style: none;
    font-size: 15px; line-height: 21px; color: var(--text-white);
  }
  .contact-list li { display: flex; align-items: center; gap: 9px; }
  .contact-icon { width: 12px; height: 12px; flex: none; }
</style>
</head>
<body>
<main class="canvas">

  <section class="card card-front" aria-label="Business card front">
    <div class="front-logo">ESN</div>
    <div class="front-tagline-top">Every Shelf Set</div>
    <div class="front-tagline-main">NEATLY</div>
    <div class="front-social">
      <span class="social-square"></span>
      <span>everyshelfsetneatly</span>
    </div>
  </section>

  <section class="card card-back" aria-label="Business card back">
    <svg class="back-wave" viewBox="0 0 560 320" preserveAspectRatio="none" aria-hidden="true">
      <path fill="#ffffff" d="M0,266 C110,272 230,258 330,236 C380,224 420,208 452,192 C400,228 320,266 220,286 C140,300 60,302 0,300 Z"/>
      <path fill="#0a7fe0" d="M0,292 C150,300 290,282 392,236 C462,202 510,166 560,150 L560,320 L0,320 Z"/>
    </svg>

    <div class="back-logo">ESN</div>
    <div class="owner-name">Lorna M. Pelham</div>
    <div class="owner-role">Owner</div>

    <ul class="contact-list">
      <li>
        <svg class="contact-icon" viewBox="0 0 12 12" aria-hidden="true"><path fill="#0a7fe0" d="M2.3 1l2 2.2-1 1.3c.8 1.6 1.9 2.7 3.3 3.4l1.3-1 2.1 2-1.2 1.8C4.5 10.4 1.4 7.3.6 2.5z"/></svg>
        <span>418-552-7094</span>
      </li>
      <li>
        <svg class="contact-icon" viewBox="0 0 12 12" aria-hidden="true"><rect x="0.5" y="2" width="11" height="8" fill="#0a7fe0"/><path d="M1 2.6 6 6.6 11 2.6" stroke="#0b0b0c" stroke-width="1" fill="none"/></svg>
        <span>info@esnorganized-example.com</span>
      </li>
      <li>
        <svg class="contact-icon" viewBox="0 0 12 12" aria-hidden="true"><g fill="none" stroke="#0a7fe0" stroke-width="1.6"><rect x="1" y="5" width="6" height="3" rx="1.5" transform="rotate(-45 4 6.5)"/><rect x="5" y="4" width="6" height="3" rx="1.5" transform="rotate(-45 8 5.5)"/></g></svg>
        <span>www.esnorganized-example.com</span>
      </li>
    </ul>
  </section>

</main>
</body>
</html>
```